Income Tax Business Cards - Updates

Need to update these business cards while keeping all the same wording but just update them and make them look nicer and more modern/ on brand with our brand.

Industry/Entity Type

finance

Contact Information for Business Card

we have multiple locations so will just need to easily be able to change the address and phone numbers

Colors

Designer to choose colors to be used in the design.

```html
<!DOCTYPE html>
<html lang="en">
<head>
<meta charset="utf-8">
<title>Ledger One Financial Group – Business Cards</title>
<link rel="stylesheet" href="https://fonts.googleapis.com/css2?family=Montserrat:wght@400;500;700;800&display=swap">
<style>
  :root {
    --brand-green: #0f5130;
    --brand-red: #c01f26;
    --brand-red-bright: #e0363c;
    --paper: #ffffff;
    --ink: #2b2b2b;
    --backdrop: #2a2a2a;
  }
  * { box-sizing: border-box; margin: 0; padding: 0; }
  html, body {
    width: 1200px; height: 900px; overflow: hidden;
    background: var(--backdrop);
    font-family: "Montserrat", Arial, sans-serif;
  }
  .card {
    position: absolute; left: 240px;
    width: 720px; height: 400px;
    border-radius: 26px; overflow: hidden;
  }

  /* Shared brand name */
  .brand-name {
    font-weight: 700; line-height: 1.1; letter-spacing: 0.5px;
    display: flex; align-items: center; gap: 12px;
  }
  .brand-name__dot { width: 14px; height: 14px; border-radius: 50%; background: currentColor; flex: none; }

  .pill {
    position: absolute; background: var(--brand-red); color: var(--paper);
    font-weight: 800; text-transform: uppercase; border-radius: 999px;
    white-space: nowrap;
  }
  .amount { color: var(--brand-red); }

  /* Front */
  .card--front { top: 35px; background: var(--brand-green); color: var(--paper); }
  .card--front .brand-name {
    position: absolute; top: 70px; left: 0; right: 0; justify-content: center;
    font-size: 40px;
  }
  .card--front .pill {
    top: 200px; left: 50%; transform: translateX(-50%);
    font-size: 22px; padding: 6px 26px;
  }
  .front-offer {
    position: absolute; bottom: 62px; left: 0; right: 0; text-align: center;
    font-size: 36px; font-weight: 800; text-transform: uppercase; letter-spacing: 1px;
  }
  .card--front .amount { color: var(--brand-red-bright); }

  /* Back */
  .card--back { top: 465px; background: var(--paper); }
  .back-wave { position: absolute; inset: 0; width: 720px; height: 400px; }
  .card--back .brand-name {
    position: absolute; top: 52px; left: 60px; width: 300px;
    font-size: 30px; color: var(--brand-green);
  }
  .divider { position: absolute; top: 40px; left: 380px; width: 2px; height: 150px; background: var(--brand-red); }
  .contact {
    position: absolute; top: 48px; left: 410px; color: var(--ink);
    font-size: 20px; font-weight: 500; line-height: 1.35; font-style: normal;
  }
  .contact__phone {
    display: flex; align-items: center; gap: 8px; margin-top: 8px;
    color: var(--brand-green); font-weight: 700; font-size: 24px;
  }
  .card--back .pill { top: 200px; left: 205px; font-size: 28px; padding: 6px 28px; }
  .back-offer {
    position: absolute; top: 262px; left: 0; right: 0; text-align: center;
    color: var(--paper); text-transform: uppercase; font-weight: 800;
  }
  .back-offer__amount-line { font-size: 46px; line-height: 1; letter-spacing: 1px; }
  .back-offer__advance { font-size: 34px; line-height: 1.2; letter-spacing: 1px; }
  .back-offer__note { font-size: 16px; font-weight: 700; letter-spacing: 1px; margin-top: 4px; }
</style>
</head>
<body>
  <section class="card card--front">
    <div class="brand-name"><span class="brand-name__dot"></span>Ledger One Financial Group</div>
    <div class="pill">File your taxes here</div>
    <p class="front-offer">Up to <span class="amount">&amp;6000</span> same day advance</p>
  </section>

  <section class="card card--back">
    <svg class="back-wave" viewBox="0 0 720 400" aria-hidden="true">
      <path d="M0 205 C 220 195, 430 210, 720 345 L720 400 L0 400 Z" fill="var(--brand-green)"/>
      <path d="M0 205 C 220 195, 430 210, 720 345" fill="none" stroke="var(--brand-red)" stroke-width="5"/>
    </svg>
    <div class="brand-name"><span class="brand-name__dot"></span>Ledger One Financial Group</div>
    <div class="divider"></div>
    <address class="contact">
      118 Meridian Ave<br>Ste 410<br>Westbrook QC 3190
      <div class="contact__phone">
        <svg width="20" height="20" viewBox="0 0 24 24" aria-hidden="true"><path fill="var(--brand-red)" d="M6.6 10.8a15.1 15.1 0 0 0 6.6 6.6l2.2-2.2c.3-.3.7-.4 1-.2 1.1.4 2.3.6 3.6.6.6 0 1 .4 1 1V20c0 .6-.4 1-1 1A17 17 0 0 1 3 4c0-.6.4-1 1-1h3.5c.6 0 1 .4 1 1 0 1.3.2 2.5.6 3.6.1.3 0 .7-.2 1z"/></svg>
        (555) 555-0147
      </div>
    </address>
    <div class="pill">Free estimates!</div>
    <div class="back-offer">
      <p class="back-offer__amount-line">Up to <span class="amount">&amp;6000</span></p>
      <p class="back-offer__advance">Same day advance</p>
      <p class="back-offer__note">On approved tax returns!</p>
    </div>
  </section>
</body>
</html>
```